brightquokka.net we need a webpage designed for our new product

We need a webpage designed for our new range of products from our new brand. We have had a logo designed on sketchharbor (see attached) and we want to keep to this theme. Our first product is a range of affordable app controlled LED lightbulbs.

I have added some photos that we think is good inspirational material and would be good as a background to this website, but we want the site to look modern but not conventional. We would like something that makes our company look quirky not corporate.

Thats it

Target Market(s)

Our product is being stocked by big name online retailers in the UK, the page will get link through hits from our app. Our target market is gadget freaks of all ages.

Industry/Entity Type

It Company

Requirements
Must have
• We are going to need a help page, text to be uploaded next few days.

We need a contact page.

design my work on iOS and Android as most people will access page through their handset or tablet.
Should not have
• We do not want anything too corporate.

```html
<!DOCTYPE html>
<html lang="en">
<head>
<meta charset="utf-8">
<title>Bright Quokka – LED Lighting</title>
<link href="https://fonts.googleapis.com/css2?family=PT+Sans:wght@400;700&family=Arimo:wght@400;700&display=swap" rel="stylesheet">
<style>
:root{
  --green:#34a73a;
  --green-text:#2fa137;
  --white:#ffffff;
  --ink:#444444;
  --body:#333333;
  --muted:#777777;
  --line:#dddddd;
  --nav:#262626;
  --field:#e5e5e5;
}
*{margin:0;padding:0;box-sizing:border-box}
html,body{width:1200px;height:972px;overflow:hidden}
body{background:var(--green);position:relative;font-family:"PT Sans",sans-serif;color:var(--body)}
.abs{position:absolute}
.panel{left:102px;top:92px;width:996px;height:644px;background:var(--white);border-radius:8px}
.tagline{left:119px;top:103px;font:12px "Arimo",sans-serif;color:var(--muted)}
.search{left:873px;top:97px;width:215px;height:26px;background:var(--field);border-radius:6px}
.search svg{position:absolute;right:14px;top:5px}
.hero{left:109px;top:130px;width:982px;height:351px;background:linear-gradient(100deg,#5b3a28 0%,#8a5a3f 25%,#b08f7e 50%,#7b5e55 75%,#3d3430 100%)}
.brand-tab{left:464px;top:0;width:249px;height:196px}
.brand-name{left:464px;top:121px;width:249px;text-align:center;font-weight:700;font-size:13px;letter-spacing:1px;color:var(--green-text)}
.cart-note{left:833px;top:11px;font:11px "Arimo",sans-serif;color:#b9f0bc;white-space:nowrap}
.cart-note b{color:var(--white);font-family:"PT Sans",sans-serif;font-size:12px;margin-left:4px}
.key-tab{left:1068px;top:0}
.cart-icon{left:1005px;top:38px}
.cart-label{left:1050px;top:46px;color:var(--white);font-size:13px;font-weight:700;line-height:14px}
.main-nav{left:109px;top:481px;width:982px;height:52px;background:var(--nav)}
.main-nav a{position:absolute;top:0;height:52px;transform:translateX(-50%);color:var(--white);text-decoration:none;font:17px "Arimo",sans-serif;line-height:54px;white-space:nowrap}
.main-nav a.home{left:11px;top:9px;height:35px;width:105px;transform:none;line-height:36px;text-align:center;background:var(--green);border-radius:7px}
.main-nav .sep{position:absolute;top:10px;width:1px;height:32px;background:#4a4a4a}
h2.section{position:absolute;font-size:24px;font-weight:700;color:var(--ink);white-space:nowrap}
.deal-box{left:112px;top:584px;width:603px;height:140px;border:1px solid var(--line)}
.deal-split{left:416px;top:591px;width:1px;height:126px;background:var(--line)}
.product-shot{width:90px;height:105px;border-radius:45px 45px 20px 20px;background:radial-gradient(circle at 50% 35%,#f2f2f2,#c9c9c9 60%,#9a9a9a)}
.product-title{font-size:18px;font-weight:700;color:var(--ink);white-space:nowrap}
.product-desc{font-size:11px;line-height:15px;color:var(--body);text-align:justify;width:170px;letter-spacing:.3px}
.price{font-size:11px;color:var(--green-text)}
.add-cart{width:77px;height:27px;border-radius:8px;background:linear-gradient(#9c9c9c,#6d6d6d);color:var(--white);font-size:12px;font-weight:700;text-align:center;line-height:27px}
.blog-box{left:739px;top:584px;width:351px;height:140px;border:1px solid var(--line);font-size:11px;line-height:18px;color:var(--body)}
.blog-box .lead{position:absolute;left:11px;top:11px;color:var(--green-text);font-weight:700}
.blog-box .by{position:absolute;right:11px;top:7px}
.blog-box .by b{color:#000}
.blog-box .text{position:absolute;left:11px;top:27px;width:328px;text-align:justify;letter-spacing:.2px}
.blog-box .posted{position:absolute;left:11px;top:109px;font-weight:700;color:#000}
.blog-box .more{position:absolute;right:11px;top:114px;color:var(--green-text);font-weight:700}
.foot-head{position:absolute;top:769px;color:var(--white);font-size:20px;font-weight:700;white-space:nowrap}
.foot-head::before{content:"";display:inline-block;border-left:6px solid var(--white);border-top:6px solid transparent;border-bottom:6px solid transparent;margin-right:9px;vertical-align:1px}
.foot-list{position:absolute;top:809px;list-style:none;font:13px "Arimo",sans-serif;line-height:18px;color:var(--white)}
.foot-list li::before{content:"";display:inline-block;width:7px;height:7px;border-radius:50%;background:var(--white);margin-right:8px;vertical-align:1px}
.foot-blog{left:551px;top:802px;width:302px;font-size:11px;line-height:18px;color:var(--white);font-weight:700;text-align:justify}
.foot-by{left:795px;top:782px;font-size:11px;color:var(--white);font-weight:700}
.foot-posted{left:551px;top:884px;font-size:11px;color:var(--white);font-weight:700}
.contact-lines{left:923px;top:809px;font:13px "Arimo",sans-serif;line-height:18px;color:var(--white);white-space:nowrap}
.foot-nav{left:0;top:920px;width:1200px;text-align:center;font-size:13px;color:var(--white);word-spacing:3px;white-space:nowrap}
.foot-nav span{margin:0 10px}
.copyright{left:0;top:943px;width:1200px;text-align:center;font:13px "Arimo",sans-serif;color:var(--white);white-space:nowrap}
.copyright span{margin:0 10px}
</style>
</head>
<body>
<div class="abs panel"></div>
<div class="abs tagline">Ipsum is simply dummy text of the printing and</div>
<div class="abs search">
  <svg width="20" height="16" viewBox="0 0 20 16"><circle cx="7" cy="6" r="5" fill="none" stroke="#34a73a" stroke-width="2"/><line x1="11" y1="10" x2="17" y2="14" stroke="#34a73a" stroke-width="3" stroke-linecap="round"/></svg>
</div>

<div class="abs hero" role="img" aria-label="Blurred photo of a white ceramic lamp in a lighting shop"></div>

<svg class="abs brand-tab" viewBox="0 0 249 196" width="249" height="196">
  <defs><linearGradient id="tabFill" x1="0" y1="0" x2="0" y2="1"><stop offset="0" stop-color="#ffffff"/><stop offset="1" stop-color="#dcdcdc"/></linearGradient></defs>
  <polygon points="0,0 249,0 249,112 124,196 0,112" fill="url(#tabFill)"/>
</svg>
<div class="abs brand-name">BRIGHTQUOKKA</div>

<div class="abs cart-note">You have no item &nbsp;in your Cart <b>Checkout »</b></div>
<svg class="abs key-tab" width="24" height="37" viewBox="0 0 24 37">
  <polygon points="0,0 24,0 24,28 12,37 0,28" fill="#d9f2da"/>
  <circle cx="10" cy="13" r="4" fill="none" stroke="#34a73a" stroke-width="2"/>
  <line x1="13" y1="16" x2="18" y2="21" stroke="#34a73a" stroke-width="2.5"/>
</svg>
<svg class="abs cart-icon" width="40" height="48" viewBox="0 0 40 48">
  <path d="M2 4 L9 4 L12 30 L36 30 L38 12 L11 12" fill="none" stroke="#9fe5a3" stroke-width="3"/>
  <rect x="12" y="14" width="24" height="14" fill="#5fd066"/>
  <circle cx="15" cy="40" r="4" fill="#9fe5a3"/><circle cx="32" cy="40" r="4" fill="#9fe5a3"/>
</svg>
<div class="abs cart-label">CART<br><i>(empty)</i></div>

<nav class="abs main-nav">
  <a class="home" href="#">Home</a>
  <span class="sep" style="left:140px"></span>
  <a href="#" style="left:200px">About us</a>
  <span class="sep" style="left:279px"></span>
  <a href="#" style="left:358px">Buy LED</a>
  <span class="sep" style="left:431px"></span>
  <a href="#" style="left:497px">Why Led</a>
  <span class="sep" style="left:567px"></span>
  <a href="#" style="left:642px">Which Led</a>
  <span class="sep" style="left:720px"></span>
  <a href="#" style="left:776px">FAQ</a>
  <span class="sep" style="left:840px"></span>
  <a href="#" style="left:915px">Contact us</a>
</nav>

<h2 class="section" style="left:113px;top:546px">This Weeks Deal!</h2>
<div class="abs deal-box"></div>
<div class="abs deal-split"></div>

<div class="abs product-shot" style="left:122px;top:600px" role="img" aria-label="100w LED flood bulb"></div>
<div class="abs product-title" style="left:226px;top:602px">100w Led Flood</div>
<div class="abs product-desc" style="left:228px;top:628px">Lorem Ipsum is simply dummy text of the printing and..</div>
<div class="abs price" style="left:228px;top:663px">$99.00</div>
<div class="abs add-cart" style="left:222px;top:685px">Add to Cart</div>

<div class="abs product-shot" style="left:431px;top:600px" role="img" aria-label="100w LED flood bulb"></div>
<div class="abs product-title" style="left:535px;top:602px">100w Led Flood</div>
<div class="abs product-desc" style="left:537px;top:628px">Lorem Ipsum is simply dummy text of the printing and..</div>
<div class="abs price" style="left:537px;top:663px">$99.00</div>
<div class="abs add-cart" style="left:531px;top:685px">Add to Cart</div>

<h2 class="section" style="left:741px;top:545px">Blog</h2>
<div class="abs blog-box">
  <div class="lead">Lorem Ipsum is simply dummy</div>
  <div class="by">By : <b>Admin</b></div>
  <div class="text">text of the printing and typesetting industry. Lorem Ipsum has been the industry's standard dummy text ever since the 1500s, when an unknown printer took a galley of type and scrambled it to make a type specimen book.</div>
  <div class="posted">Posted in news on 29-04-2014</div>
  <div class="more">Readmore</div>
</div>

<div class="foot-head" style="left:122px">Support</div>
<ul class="foot-list" style="left:122px"><li>Warranty and Returns</li><li>Order Status</li><li>Shipment Tracking</li><li>FAQ's</li></ul>
<div class="foot-head" style="left:342px">Account</div>
<ul class="foot-list" style="left:342px"><li>Warranty and Returns</li><li>Order Status</li><li>Shipment Tracking</li><li>FAQ's</li></ul>
<div class="foot-head" style="left:551px">Blog</div>
<div class="abs foot-by">By : Admin</div>
<div class="abs foot-blog">text of the printing and typesetting industry. Lorem Ipsum has been the industry's standard dummy text ever since the 1500s, when an unknown printer took a galley of type and scrambled it to make</div>
<div class="abs foot-posted">Posted in news on 29-04-2014</div>
<div class="foot-head" style="left:923px">Contact us</div>
<div class="abs contact-lines">Office (888) 555-5555<br>Mobile (888) 555-5555<br>Fax (888) 555-5555<br>support@brightquokka.net</div>

<div class="abs foot-nav">Home<span>|</span>About us<span>|</span>Buy LED<span>|</span>Why Led<span>|</span>Which Led<span>|</span>FAQ<span>|</span>Contact us</div>
<div class="abs copyright">Copyright © 2010 - 2014 bright quokka. All Rights Reserved &nbsp; Terms and Conditions<span>|</span>&nbsp; Privacy Policy</div>
</body>
</html>
```